Verodex business card

Business card for sustainable investment company called "Verodex". Verodex is an exchange platform selling carbon credits between buyers and sellers. Carbon Credits are an environmental commodity for reducing global carbon emissions.

the card should obviously have our logo and the theme should be sustainability/environment mixed with a trading platform.

Contact Information for Business Card

Logo, Name, Title, Phone, Email

Colors
0054AA
0677BA
7BADD7
CADEEF
E8F1F8
0094D4
00A9DD
6FCCEA
C7EBF8
E9F6FB
00AB8E
00BBA5
67D7C9
C6EFE9
E9F9F6
59FF00
82FF00
B8FF75
E3FFCB
F4FFEA

```html
<!DOCTYPE html>
<html lang="en">
<head>
<meta charset="utf-8">
<title>Verodex business card</title>
<link rel="stylesheet" href="https://fonts.googleapis.com/css2?family=Montserrat:wght@400;500;700&display=swap">
<style>
  :root {
    --navy: #1a2b58;
    --navy-deep: #14224a;
    --blue: #4a7cc8;
    --cyan: #45c8ec;
    --white: #ffffff;
    --page: #e6e8ec;
  }
  * { margin: 0; padding: 0; box-sizing: border-box; }
  html, body { width: 1200px; height: 960px; overflow: hidden; }
  body {
    background: var(--page);
    font-family: "Montserrat", sans-serif;
    position: relative;
  }
  .card {
    position: absolute;
    left: 250px;
    width: 700px;
    height: 400px;
    border-radius: 22px;
    overflow: hidden;
    box-shadow: 0 6px 18px rgba(20, 34, 74, 0.18);
  }
  .card-front {
    top: 60px;
    background: linear-gradient(135deg, #22386a 0%, var(--navy) 45%, var(--navy-deep) 100%);
    display: flex;
    align-items: center;
    justify-content: center;
    gap: 22px;
  }
  .card-back { top: 500px; background: var(--white); }
  .card-back .wave { position: absolute; inset: 0; }
  .brand-dot {
    width: 58px; height: 58px; border-radius: 50%;
    background: var(--cyan);
  }
  .brand-dot.small { width: 40px; height: 40px; }
  .wordmark {
    font-weight: 700;
    letter-spacing: 1px;
    text-transform: uppercase;
  }
  .card-front .wordmark { color: var(--white); font-size: 64px; }
  .back-brand {
    position: absolute;
    left: 78px; top: 118px;
    display: flex; align-items: center; gap: 16px;
  }
  .back-brand .wordmark { color: var(--navy); font-size: 42px; }
  .contact {
    position: absolute;
    right: 42px; top: 142px;
    text-align: right;
    color: var(--white);
  }
  .contact-name { font-weight: 700; font-size: 24px; letter-spacing: 0.5px; text-transform: uppercase; }
  .contact-title { font-weight: 400; font-size: 16px; margin-top: 2px; margin-bottom: 22px; }
  .contact-line {
    display: flex; justify-content: flex-end; align-items: center; gap: 12px;
    font-size: 16px; font-weight: 400; line-height: 30px;
  }
  .contact-line svg { width: 16px; height: 16px; fill: var(--white); }
</style>
</head>
<body>

<section class="card card-front">
  <span class="brand-dot"></span>
  <span class="wordmark">Verodex</span>
</section>

<section class="card card-back">
  <svg class="wave" viewBox="0 0 700 400" preserveAspectRatio="none" aria-hidden="true">
    <defs>
      <linearGradient id="band" x1="0" y1="1" x2="1" y2="0">
        <stop offset="0" stop-color="#45c8ec"/>
        <stop offset="0.5" stop-color="#3aa6e2"/>
        <stop offset="1" stop-color="#4a7cc8"/>
      </linearGradient>
      <path id="sweep" d="M570,0 C480,40 450,150 410,230 C370,300 210,322 0,338 L0,420 L720,420 L720,0 Z"/>
    </defs>
    <use href="#sweep" transform="translate(-30,-26)" fill="#1a2b58"/>
    <use href="#sweep" transform="translate(-25,-22)" fill="#ffffff"/>
    <use href="#sweep" transform="translate(-21,-18)" fill="url(#band)"/>
    <use href="#sweep" transform="translate(-6,-5)" fill="#ffffff"/>
    <use href="#sweep" fill="#1a2b58"/>
  </svg>

  <div class="back-brand">
    <span class="brand-dot small"></span>
    <span class="wordmark">Verodex</span>
  </div>

  <div class="contact">
    <p class="contact-name">Daniel Marsh</p>
    <p class="contact-title">Co-Founder</p>
    <p class="contact-line">555-210-4836
      <svg viewBox="0 0 24 24"><path d="M6.6 10.8a15.1 15.1 0 0 0 6.6 6.6l2.2-2.2a1 1 0 0 1 1-.25 11.4 11.4 0 0 0 3.6.57 1 1 0 0 1 1 1V20a1 1 0 0 1-1 1A17 17 0 0 1 3 4a1 1 0 0 1 1-1h3.5a1 1 0 0 1 1 1c0 1.25.2 2.45.57 3.57a1 1 0 0 1-.25 1z"/></svg>
    </p>
    <p class="contact-line">info@verodex.com
      <svg viewBox="0 0 24 24"><path d="M2 5h20v14H2z M2 5l10 8 10-8" fill="none" stroke="#fff" stroke-width="2"/></svg>
    </p>
    <p class="contact-line">www.verodex.com
      <svg viewBox="0 0 24 24"><circle cx="12" cy="12" r="9" fill="none" stroke="#fff" stroke-width="2"/><path d="M3 12h18M12 3c3 3 3 15 0 18M12 3c-3 3-3 15 0 18" fill="none" stroke="#fff" stroke-width="1.6"/></svg>
    </p>
  </div>
</section>

</body>
</html>
```